Business Card Design Competition

We need a business card design for our Internet Marketing company. We require both front and back designs and the final card must be 89x53mm in size, plus crop marks to 91x55mm. Colours as per logo, plus perhaps black and/or grey (#828282).
Final text must be editable (if you can supply an editable Fireworks PNG, even better)...
FRONT TEXT:
Full Name
Position
Address Line
Suburb, State, Postcode
Phone: 0000 000 000
Mobile: 0000 000 000
Email: xxx@brightlanemedia.com.au
Web: www.brightlanemedia.com.au
Rear of card should be a fresh design plus our slogan text: "Getting You Noticed" in large font, then in small text "Kestrel Holdings Pty Ltd (ABN: 42 561 903 774)".
Target Market(s)
Small/Medium Businesses
Industry/Entity Type
Business

```html
<!DOCTYPE html>
<html lang="en">
<head>
<meta charset="utf-8">
<title>Brightlane Media – Business Card Front</title>
<link rel="stylesheet" href="https://fonts.googleapis.com/css2?family=Jura:wght@500&display=swap">
<style>
  :root {
    --bg-top: #dcdcdc;
    --bg-bottom: #ffffff;
    --band-dark: #8c8c8c;
    --band-light: #e4e4e4;
    --panel: #2e4d57;
    --panel-edge: #1f363e;
    --brand-orange: #f5a01e;
    --brand-green: #8cc63f;
  }
  html, body {
    margin: 0;
    padding: 0;
    overflow: hidden;
  }
  .card {
    position: relative;
    width: 1200px;
    height: 726px;
    overflow: hidden;
    background: linear-gradient(160deg, var(--bg-top) 0%, #ececec 55%, var(--bg-bottom) 100%);
  }
  .card__band {
    position: absolute;
    left: 0;
    top: 0;
  }
  .brand {
    position: absolute;
    left: 290px;
    top: 245px;
    display: flex;
    align-items: center;
    gap: 26px;
  }
  .brand__dot {
    width: 190px;
    height: 190px;
    border-radius: 50%;
    background: var(--brand-orange);
    flex: none;
  }
  .brand__name {
    margin: 0;
    font-family: "Jura", sans-serif;
    font-weight: 500;
    font-size: 72px;
    line-height: 0.95;
    color: var(--brand-orange);
    letter-spacing: 1px;
  }
  .brand__name span {
    display: block;
  }
</style>
</head>
<body>
<div class="card">
  <svg class="card__band" width="1200" height="726" viewBox="0 0 1200 726" aria-hidden="true">
    <defs>
      <linearGradient id="bandFill" x1="0" y1="0" x2="1" y2="0">
        <stop offset="0" stop-color="var(--band-dark)"/>
        <stop offset="0.45" stop-color="#9a9a9a"/>
        <stop offset="1" stop-color="var(--band-light)"/>
      </linearGradient>
    </defs>
    <path class="band-outer" d="M0 191 H852 A153 153 0 0 1 852 497 H0 Z" fill="url(#bandFill)"/>
    <path class="band-panel" d="M0 219 H818 A125 125 0 0 1 818 469 H0 Z" fill="var(--panel)" stroke="var(--panel-edge)" stroke-width="3"/>
  </svg>

  <div class="brand">
    <div class="brand__dot"></div>
    <h1 class="brand__name"><span>Brightlane</span><span>Media</span></h1>
  </div>
</div>
</body>
</html>
```